Lumora Systems New Website - IT Infrastructure | Smart Cabinet | Micro Data Center

We're an IT SI providing Server Room Design & Build | All-in-One Rack & Smart Cabinet | Structured Cabling | IT Relocation | Maintenance. Old website can be found at www.lumorasys.com.hk. We'd like a brand new wix website which is modern, minimalist, interactive with some animation. Website content will be mostly static and include our service, our project, news and events, about us, contacts, blogs, partners and brands, etc.

reference sites:
We'd like to see more designs referring to below

https://www.pixelvane.example/design/41736205
https://www.pixelvane.example/design/41892417
https://velbrinn.example/

Animation (scrolling effect) referring to
https://velbrinn.example/intelligence/smart-office-room/
Updates

we'd like below style.

Designs look the same

Target Market(s)

Commercials in HK

Industry/Entity Type

IT, Technology, Data Center

Coding

Coded - Design and coding required

Font styles to use
Sans Serif

Requirements
Must have
• CMS, Some Interactive Elements/ Graphics

```html
<!DOCTYPE html>
<html lang="en">
<head>
<meta charset="utf-8">
<title>Lumora Systems — IT Infrastructure</title>
<link rel="stylesheet" href="https://fonts.googleapis.com/css2?family=Montserrat:wght@400;500;600&family=Poppins:wght@400;500;600;700&display=swap">
<style>
:root{
  --navy:#0b2452;
  --navy-deep:#08204a;
  --blue:#1b55b5;
  --bright-blue:#2f6bff;
  --teal:#17a98a;
  --red:#a80d1b;
  --red-dark:#7f0712;
  --ink:#1b1b1b;
  --text:#333;
  --muted:#8a8a8a;
  --line:#c9c9c9;
  --white:#fff;
  --black:#050505;
}
*{margin:0;padding:0;box-sizing:border-box}
html,body{width:1200px;height:5115px;overflow:hidden}
body{position:relative;font-family:'Montserrat',sans-serif;color:var(--text);background:var(--white)}
.abs{position:absolute}
.h-title{font-family:'Poppins',sans-serif;font-weight:600;color:var(--ink);font-size:34px;text-align:center;white-space:nowrap}
.h-title .accent{color:var(--navy)}
.rule{position:absolute;height:3px;background:var(--red);width:130px}
.btn{position:absolute;display:flex;align-items:center;justify-content:center;border-radius:10px;font-family:'Poppins',sans-serif;font-size:14px;background:var(--navy);color:var(--white)}
.photo{position:absolute;border-radius:12px}

/* header */
.brand{left:112px;top:40px;display:flex;align-items:center;gap:12px;white-space:nowrap}
.brand-mark{width:20px;height:20px;background:var(--teal);border-radius:3px}
.brand-name{font-family:'Poppins',sans-serif;font-weight:500;font-size:30px;color:var(--blue)}
.nav{left:424px;top:50px;display:flex;gap:30px;font-size:13.5px;color:var(--ink);white-space:nowrap}
.nav .active{color:var(--teal)}
.signin{left:940px;top:38px;width:148px;height:44px;border-radius:6px;font-size:14px}

/* hero */
.hero-left{left:0;top:130px;width:610px;height:560px;background:var(--navy-deep);border-top-left-radius:46px}
.hero-photo{left:604px;top:130px;width:596px;height:560px;border-radius:0 0 46px 0;background:linear-gradient(120deg,#55606b,#c9cdd2 55%,#7b858f)}
.hero-copy{left:112px;top:280px;font-family:'Poppins',sans-serif;font-weight:600;font-size:42px;line-height:66px;color:var(--white);white-space:nowrap}
.hero-copy .hl{color:var(--bright-blue)}
.get-started{left:112px;top:476px;width:132px;height:42px;background:var(--white);color:var(--ink);border-radius:21px;font-size:13px}

/* about */
.about-mark{left:110px;top:900px;display:flex;align-items:center;gap:20px;white-space:nowrap}
.about-mark .sq{width:60px;height:60px;background:var(--teal);border-radius:8px}
.about-mark .nm{font-family:'Poppins',sans-serif;font-weight:600;font-size:40px;color:var(--blue)}
.about-text{left:640px;top:864px;width:450px;text-align:center;font-size:14px;line-height:27.5px}

/* services */
.services{left:0;top:1210px;width:1200px;height:490px;background:radial-gradient(circle at 30% 40%,#b5101f,var(--red) 50%,var(--red-dark))}
.svc-title{left:114px;top:1334px;font-family:'Poppins',sans-serif;font-weight:600;font-size:34px;color:var(--white)}
.svc-title span{color:var(--black)}
.svc-text{left:114px;top:1406px;width:450px;font-size:14.5px;line-height:31px;color:var(--white)}
.svc-card{position:absolute;width:206px;height:164px;background:var(--white);border-radius:4px;display:flex;flex-direction:column;align-items:center;justify-content:flex-end;padding-bottom:22px;text-align:center;font-family:'Poppins',sans-serif;font-size:15px;line-height:22px;color:var(--ink)}
.svc-card svg{margin-bottom:16px}
.svc-card::after{content:"";position:absolute;right:0;bottom:0;width:14px;height:14px;background:var(--black)}

/* partners */
.partners{left:0;top:2280px;width:1200px;height:366px;background:radial-gradient(circle at 50% 40%,#b8111f,var(--red) 55%,var(--red-dark))}
.partner{position:absolute;top:2456px;font-family:'Poppins',sans-serif;font-weight:700;font-size:22px;color:var(--white);letter-spacing:1px}
.partner-active{position:absolute;left:504px;top:2408px;width:216px;height:132px;background:var(--white);display:flex;align-items:center;justify-content:center;font-family:'Poppins',sans-serif;font-weight:700;font-size:26px;color:var(--ink)}

/* events */
.event{position:absolute;width:288px;height:304px;background:var(--white);box-shadow:0 4px 12px rgba(0,0,0,.18);border-radius:6px}
.event .pic{position:absolute;left:0;top:0;width:288px;height:240px;border-radius:6px 6px 0 0}
.event .cap{position:absolute;left:12px;top:258px;font-size:15px;color:var(--ink);white-space:nowrap}
.event .cap span{font-size:14px;color:#555}
.event .plus{position:absolute;right:22px;top:250px;font-size:26px;color:var(--navy);font-weight:600}
.date{position:absolute;width:62px;height:68px;background:var(--red);color:var(--white);text-align:center;font-size:19px;line-height:26px;padding-top:8px}

/* blogs */
.blogs{left:0;top:3280px;width:1200px;height:500px;background:radial-gradient(circle at 50% 30%,#b8111f,var(--red) 55%,var(--red-dark))}
.blog-text{position:absolute;text-align:center;font-size:14px;line-height:24px;color:var(--ink)}
.blog-text .more{color:#c2282f;letter-spacing:.5px}

/* contact */
.contact-bg{left:0;top:4180px;width:1200px;height:520px;background:linear-gradient(180deg,#fff,#eceef0 40%,#e3e5e8)}
.form{left:264px;top:4348px;width:670px;height:342px;background:var(--white);box-shadow:0 2px 10px rgba(0,0,0,.05)}
.field{position:absolute;border-bottom:1px solid var(--line);font-size:13px;color:var(--muted);padding-bottom:12px}

/* footer */
.footer{left:0;top:4700px;width:1200px;height:415px;background:var(--black)}
.f-brand{left:0;width:1200px;top:4786px;display:flex;justify-content:center;align-items:center;gap:18px}
.f-brand .sq{width:26px;height:26px;background:var(--white);border-radius:3px}
.f-brand .nm{font-family:'Poppins',sans-serif;font-weight:500;font-size:50px;color:var(--white)}
.f-info{position:absolute;color:var(--white);font-size:14.5px;line-height:27px;white-space:nowrap}
.copy{left:0;top:5056px;width:1200px;text-align:center;color:var(--white);font-size:13px}
</style>
</head>
<body>

<!-- Header -->
<div class="abs brand"><div class="brand-mark"></div><div class="brand-name">Lumora Systems</div></div>
<nav class="abs nav"><span class="active">Home</span><span>About Us</span><span>Our Services</span><span>Our Projects</span><span>Contact Us</span></nav>
<div class="btn signin">Sign In&nbsp;
  <svg width="12" height="13" viewBox="0 0 12 13"><circle cx="6" cy="3.5" r="3" fill="#fff"/><path d="M0 13c0-4 2.5-6 6-6s6 2 6 6z" fill="#fff"/></svg>
</div>

<!-- Hero -->
<div class="abs hero-left"></div>
<div class="abs hero-photo" role="img" aria-label="Two engineers inspecting a server rack in a data center"></div>
<div class="abs hero-copy">IT Infrastructure.<br><span class="hl">Smart Cabinet.</span><br>Micro Data Center.</div>
<div class="btn get-started">Get Started</div>

<!-- About -->
<div class="abs about-mark"><div class="sq"></div><div class="nm">Lumora Systems</div></div>
<div class="rule" style="left:800px;top:798px"></div>
<div class="abs h-title" style="left:620px;top:806px;width:490px">About <span class="accent">Lumora Systems</span></div>
<p class="abs about-text">Lumora Systems is well experienced in delivering the best in Data Center Infrastructure, Network Infrastructure, Structured Cabling, Telephony, Access Control, Video Surveillance, Audiovisual &amp; Conferencing, Relocation &amp; Migration and Maintenance solutions. Our dedication, focus, and expertise wins much recognition of many IT professionals in all industries in the region.</p>
<div class="btn" style="left:802px;top:1072px;width:126px;height:44px">Read More</div>

<!-- Services -->
<div class="abs services"></div>
<div class="abs" style="left:114px;top:1316px;width:136px;height:3px;background:#fff"></div>
<div class="abs svc-title">Our <span>Services</span></div>
<p class="abs svc-text">Lorem ipsum dolor sit amet, consectetur adipiscing elit, sed do mod tempor incididunt ut labore et dolore agna aliqua. Quis avida. isus commodo viverra acumsan lacus vel facilisis.Lorem sum dolor sit amet, consectetur dipng elit, sed do mod empor ut ore et dolore magna aliqua.</p>
<div class="btn" style="left:114px;top:1574px;width:122px;height:42px">View More</div>

<div class="svc-card" style="left:651px;top:1302px">
  <svg width="52" height="52" viewBox="0 0 52 52" fill="none" stroke="#222" stroke-width="2"><rect x="8" y="6" width="36" height="30" rx="3"/><path d="M8 16h36M8 26h36M20 36v8M32 36v8M12 46h28"/></svg>
  Data center design<br>and build</div>
<div class="svc-card" style="left:875px;top:1302px">
  <svg width="52" height="52" viewBox="0 0 52 52" fill="none" stroke="#222" stroke-width="2"><circle cx="26" cy="28" r="12"/><circle cx="26" cy="28" r="4"/><path d="M26 4v10M14 8l5 8M38 8l-5 8M8 20l8 3M44 20l-8 3M20 44v4M32 44v4"/></svg>
  Structured Cabling<br>And Fiber Backbone</div>
<div class="svc-card" style="left:651px;top:1476px">
  <svg width="52" height="52" viewBox="0 0 52 52" fill="none" stroke="#222" stroke-width="2"><ellipse cx="26" cy="12" rx="16" ry="6"/><path d="M10 12v28c0 3 7 6 16 6s16-3 16-6V12M10 22c0 3 7 6 16 6s16-3 16-6M10 31c0 3 7 6 16 6s16-3 16-6"/></svg>
  All-In-One Rack /<br>Micro-Data Center</div>
<div class="svc-card" style="left:875px;top:1476px">
  <svg width="52" height="52" viewBox="0 0 52 52" fill="none" stroke="#222" stroke-width="2"><rect x="10" y="6" width="32" height="22" rx="2"/><path d="M14 22l7-8 6 5 8-10M18 28v6M34 28v6M12 46c0-7 6-12 14-12s14 5 14 12z"/></svg>
  Audiovisual and<br>Conference Room</div>

<!-- Projects -->
<div class="rule" style="left:535px;top:1796px"></div>
<div class="abs h-title" style="left:0;top:1802px;width:1200px">Our <span class="accent">Projects</span></div>
<svg class="abs" style="left:66px;top:2016px" width="24" height="24" viewBox="0 0 24 24"><circle cx="12" cy="12" r="11" fill="#9a9a9a"/><path d="M14 7l-5 5 5 5" stroke="#fff" stroke-width="2.5" fill="none"/></svg>
<div class="photo" style="left:112px;top:1898px;width:306px;height:286px;background:linear-gradient(160deg,#1c3d7a,#3a78c9 45%,#15264a)" role="img" aria-label="Blue network patch cables in a rack"></div>
<div class="photo" style="left:448px;top:1898px;width:306px;height:286px;background:linear-gradient(160deg,#2a2a2a,#4a4a4a 50%,#151515)" role="img" aria-label="Server cabinet installed for a securities firm"></div>
<div class="abs" style="left:448px;top:1998px;width:306px;text-align:center;color:#fff;font-family:'Poppins',sans-serif;font-size:19px;line-height:29px">A renowned China<br>based Securities firm</div>
<div class="abs" style="left:448px;top:2058px;width:306px;text-align:center;color:#c2282f;font-size:11px">Learn More</div>
<div class="photo" style="left:782px;top:1898px;width:306px;height:286px;background:linear-gradient(160deg,#cfd3d8,#6c7178 55%,#2b2e33)" role="img" aria-label="Row of black smart cabinets in a server room"></div>
<svg class="abs" style="left:1114px;top:2016px" width="24" height="24" viewBox="0 0 24 24"><circle cx="12" cy="12" r="11" fill="#111"/><path d="M10 7l5 5-5 5" stroke="#fff" stroke-width="2.5" fill="none"/></svg>

<!-- Partners -->
<div class="abs partners"></div>
<div class="abs h-title" style="left:0;top:2318px;width:1200px;color:#fff">Our Partners</div>
<div class="partner" style="left:114px">CORVANE</div>
<div class="partner" style="left:326px">HALDEN</div>
<div class="partner-active">Tessaro</div>
<div class="partner" style="left:758px">ORBISIGHT</div>
<div class="partner" style="left:968px">KELMONT</div>
<div class="btn" style="left:544px;top:2566px;width:124px;height:42px;border-radius:8px">View More</div>

<!-- Events -->
<div class="rule" style="left:535px;top:2744px"></div>
<div class="abs h-title" style="left:0;top:2748px;width:1200px">Our <span class="accent">Events</span></div>
<div class="event" style="left:120px;top:2872px">
  <div class="pic" style="background:linear-gradient(170deg,#c88a4a,#6b3b22 55%,#2a1a14)" role="img" aria-label="Speaker addressing a conference audience"></div>
  <div class="cap">Event Name: <span>Lorem ipsum</span></div><div class="plus">+</div>
</div>
<div class="date" style="left:308px;top:2848px">Dec<br>23</div>
<div class="event" style="left:438px;top:2872px">
  <div class="pic" style="background:linear-gradient(170deg,#0f2a55,#3f86d6 45%,#10172a)" role="img" aria-label="Crowd at a large stage event with blue lights"></div>
  <div class="cap">Event Name: <span>Lorem ipsum</span></div><div class="plus">+</div>
</div>
<div class="date" style="left:626px;top:2848px">Dec<br>25</div>
<p class="abs" style="left:762px;top:2896px;width:340px;font-size:14px;line-height:25.5px">Lorem ipsum dolor sit amet, dipiscing elit, ed do eiusmod ncididunt ut labore et agna liqua. Quis ipsum spendisse trices gravida. aecenas cumsan lacus vel facilisis.Lorem ipsum dolor sit tonsectetur adipiscing elit, sed do iusmod didunt abore et dolore magna aliqua. Quis endisse avida. Risus commodo aecenas cumsan lacus vel facilisis.</p>
<svg class="abs" style="left:762px;top:3110px" width="22" height="22" viewBox="0 0 24 24"><circle cx="12" cy="12" r="11" fill="#9a9a9a"/><path d="M14 7l-5 5 5 5" stroke="#fff" stroke-width="2.5" fill="none"/></svg>
<svg class="abs" style="left:794px;top:3110px" width="22" height="22" viewBox="0 0 24 24"><circle cx="12" cy="12" r="11" fill="#111"/><path d="M10 7l5 5-5 5" stroke="#fff" stroke-width="2.5" fill="none"/></svg>

<!-- Blogs -->
<div class="abs blogs"></div>
<div class="abs" style="left:535px;top:3332px;width:130px;height:3px;background:#fff"></div>
<div class="abs h-title" style="left:0;top:3336px;width:1200px;color:#fff">Our Blogs</div>
<p class="abs" style="left:260px;top:3392px;width:680px;text-align:center;color:#fff;font-size:14px;line-height:24px">Lorem ipsum dolor sit amet, consectetur adipiscing elit, sed do eiusmod tempor<br>Quis ipsum</p>
<div class="btn" style="left:516px;top:3458px;width:168px;height:42px;border-radius:12px">View All Blogs &rsaquo;</div>
<div class="abs" style="left:110px;top:3456px;width:296px;height:428px;background:linear-gradient(160deg,#e8e6e1,#9b8f80 50%,#3c5b3c)" role="img" aria-label="Two colleagues reviewing work on a laptop"></div>
<div class="abs" style="left:430px;top:3530px;width:318px;height:490px;background:linear-gradient(170deg,#1a2d55,#2f6bbd 40%,#0c1730)" role="img" aria-label="Two technicians standing between server racks"></div>
<div class="abs" style="left:772px;top:3456px;width:316px;height:428px;background:linear-gradient(170deg,#0f2246,#1f4f96 50%,#0a1530)" role="img" aria-label="Engineer with a laptop in a data center aisle"></div>
<div class="blog-text" style="left:110px;top:3898px;width:296px">Lorem ipsum dolor sit amet,<br>consectetur ipiscing elit, sed do<br>eiusmod tempor &nbsp;et dolore magna<br><span class="more">LEARN MORE &#10230;</span></div>
<div class="blog-text" style="left:430px;top:4026px;width:318px">Lorem ipsum dolor sit amet,<br>consectetur ipiscing elit, sed do<br>eiusmod tempor &nbsp;et dolore magna<br><span class="more" style="line-height:40px">LEARN MORE &#10230;</span></div>
<div class="blog-text" style="left:772px;top:3898px;width:316px">Lorem ipsum dolor sit amet,<br>consectetur ipiscing elit, sed do<br>eiusmod tempor &nbsp;et dolore magna<br><span class="more">LEARN MORE &#10230;</span></div>

<!-- Contact -->
<div class="abs contact-bg"></div>
<div class="rule" style="left:535px;top:4224px"></div>
<div class="abs h-title" style="left:0;top:4228px;width:1200px">Contact <span class="accent">Us</span></div>
<div class="abs form"></div>
<div class="field" style="left:300px;top:4392px;width:290px">First Name</div>
<div class="field" style="left:610px;top:4392px;width:290px">Last Name</div>
<div class="field" style="left:300px;top:4472px;width:290px">Email</div>
<div class="field" style="left:610px;top:4472px;width:290px">Subject</div>
<div class="field" style="left:300px;top:4576px;width:600px">Text Here...</div>
<div class="btn" style="left:530px;top:4632px;width:138px;height:42px;border-radius:12px">Submit Now</div>

<!-- Footer -->
<div class="abs footer"></div>
<div class="abs f-brand"><div class="sq"></div><div class="nm">Lumora Systems</div></div>
<svg class="abs" style="left:140px;top:4940px" width="22" height="22" viewBox="0 0 24 24"><path d="M6 2l4 5-2 3c1 3 3 5 6 6l3-2 5 4-2 4C10 22 2 14 2 4z" fill="#fff"/></svg>
<div class="f-info" style="left:190px;top:4938px">+852 2000 4815</div>
<svg class="abs" style="left:420px;top:4936px" width="18" height="26" viewBox="0 0 18 26"><path d="M9 0a9 9 0 0 1 9 9c0 7-9 17-9 17S0 16 0 9a9 9 0 0 1 9-9z" fill="#fff"/><circle cx="9" cy="9" r="3.5" fill="#050505"/></svg>
<div class="f-info" style="left:462px;top:4910px;width:260px;text-align:center">Rm 908, 9/F, Harbourline Centre,<br>12 Kiln Road, San Po Kong,<br>Kowloon, Hong Kong</div>
<svg class="abs" style="left:816px;top:4942px" width="26" height="20" viewBox="0 0 26 20" fill="none" stroke="#fff" stroke-width="2"><rect x="1" y="1" width="24" height="18" rx="2"/><path d="M1 3l12 9 12-9"/></svg>
<div class="f-info" style="left:868px;top:4938px">marketing@lumorasys.com.hk</div>
<div class="abs copy">&copy; 2023 &nbsp;Lumora Systems | All Rights Reserved</div>

</body>
</html>
```